Postcard Design

A house cleaning business. Focus on time saving and stress free. Free estimates. Want it to state that we can make your home sparkle or shine. I have been using the colors purple and black in the logo which I will attach.

Reason: I need a few more days to decide on this. Thank you

Industry/Entity Type

House

Colors
886aae
6b449b

Requirements
Must have
• website www.maplecrestmaids.us
phone # 555-316-2984

```html
<!DOCTYPE html>
<html lang="en">
<head>
<meta charset="UTF-8">
<title>Maplecrest Maids – Postcard</title>
<link rel="stylesheet" href="https://fonts.googleapis.com/css2?family=Marcellus+SC&family=Jost:wght@500;700&display=swap">
<style>
  :root {
    --canvas-bg: #e9e7e3;
    --purple-light: #886aae;
    --purple-deep: #6b449b;
    --headline: #6f4fa6;
    --white: #ffffff;
    --ink: #2a2420;
    --wood-dark: #5a3418;
    --wood-mid: #9a6232;
    --stone: #b9a58c;
    --window: #dfe6ee;
  }
  * { box-sizing: border-box; margin: 0; padding: 0; }
  html, body {
    width: 1200px;
    height: 800px;
    overflow: hidden;
    background: var(--canvas-bg);
  }
  .canvas {
    position: relative;
    width: 1200px;
    height: 800px;
    display: flex;
    align-items: center;
    justify-content: center;
  }
  .postcard {
    position: relative;
    width: 1000px;
    height: 628px;
    overflow: hidden;
    box-shadow: 0 6px 18px rgba(0, 0, 0, 0.25);
  }
  .kitchen-photo {
    position: absolute;
    inset: 0;
    background:
      linear-gradient(180deg, rgba(255,255,255,0.35) 0%, rgba(255,255,255,0) 18%),
      radial-gradient(ellipse 28% 40% at 35% 45%, var(--window) 0%, rgba(223,230,238,0) 100%),
      radial-gradient(ellipse 22% 45% at 88% 55%, var(--window) 0%, rgba(223,230,238,0) 100%),
      linear-gradient(180deg, transparent 62%, var(--stone) 64%, #8c7b68 78%, var(--wood-dark) 100%),
      linear-gradient(90deg, var(--wood-mid) 0%, #b57a42 28%, #c9a77f 55%, #a99a8a 75%, #cfd3d8 100%);
  }
  .headline {
    position: absolute;
    top: 28px;
    left: 0;
    width: 100%;
    text-align: center;
    font-family: "Marcellus SC", serif;
    font-size: 48px;
    letter-spacing: 1px;
    color: var(--headline);
    text-shadow: 0 1px 2px rgba(255,255,255,0.4);
  }
  .intro {
    position: absolute;
    top: 88px;
    left: 0;
    width: 100%;
    text-align: center;
    font-family: "Jost", sans-serif;
    font-weight: 500;
    font-size: 30px;
    line-height: 38px;
    color: var(--white);
    text-shadow: 0 1px 3px rgba(0,0,0,0.45);
  }
  .brand {
    position: absolute;
    top: 300px;
    left: 320px;
    display: flex;
    align-items: center;
    gap: 12px;
  }
  .brand-mark {
    width: 22px;
    height: 22px;
    border-radius: 50%;
    background: var(--purple-deep);
  }
  .brand-name {
    font-family: "Jost", sans-serif;
    font-weight: 700;
    font-size: 40px;
    color: var(--purple-deep);
  }
  .benefits {
    position: absolute;
    top: 362px;
    left: 354px;
    font-family: "Jost", sans-serif;
    font-weight: 500;
    font-size: 24px;
    color: var(--white);
    text-shadow: 0 1px 3px rgba(0,0,0,0.5);
  }
  .tagline {
    position: absolute;
    top: 520px;
    left: 345px;
    font-family: "Jost", sans-serif;
    font-weight: 700;
    font-size: 22px;
    letter-spacing: 1px;
    color: var(--ink);
    transform: rotate(3deg);
    transform-origin: left center;
  }
  .call-to-action {
    position: absolute;
    top: 568px;
    left: 182px;
    font-family: "Jost", sans-serif;
    font-weight: 700;
    font-size: 36px;
    color: var(--white);
    text-shadow: 0 1px 3px rgba(0,0,0,0.5);
  }
  .contact {
    position: absolute;
    right: 24px;
    bottom: 16px;
    text-align: right;
    font-family: "Jost", sans-serif;
    font-weight: 700;
    font-size: 20px;
    line-height: 26px;
    color: var(--white);
    text-shadow: 0 1px 3px rgba(0,0,0,0.6);
  }
</style>
</head>
<body>
  <main class="canvas">
    <section class="postcard">
      <div class="kitchen-photo" role="img" aria-label="Photo of a bright kitchen with wooden cabinets, a granite counter, stainless appliances and snowy windows, with a silhouette of a housekeeper dusting"></div>
      <h1 class="headline">A Sparking Shine, Every Time</h1>
      <p class="intro">
        Maplecrest Maids cleaning company offers old fashion,<br>
        high-quality home cleaning services.<br>
        Our professionals are insured and bonded.
      </p>
      <div class="brand">
        <span class="brand-mark"></span>
        <span class="brand-name">Maplecrest Maids</span>
      </div>
      <p class="benefits">Time saving. Stress free.</p>
      <p class="tagline">We can make your house sparkle!</p>
      <p class="call-to-action">Call today for a free estimate.</p>
      <p class="contact">
        555-316-2984<br>
        www.maplecrestmaids.us
      </p>
    </section>
  </main>
</body>
</html>
```